Business cards and stationary design

We just completed the design of our new logo and we need to print new business cards and letterhead for our nonprofit. We are looking for a fresh new design that shows off our new logo. On letterhead, we must have a column on the right or left to include our Board of Directors (up to 45 names) (see attachment)

Industry/Entity Type

Non-Profit

Contact Information for Business Card

Standard business card with name, title, Company name, mailing address phone numbers, email address and website. Tagline on back "Bringing the homeless home"

Font styles to use
Sans Serif

Requirements
Must have
• include pertinent information above
• new logo
• fonts compatible with logo
• should use logo colors only
Nice to have
• tag lines

```html
<!DOCTYPE html>
<html lang="en">
<head>
<meta charset="utf-8">
<title>Haven Street Center – Business Card</title>
<link href="https://fonts.googleapis.com/css2?family=Roboto:wght@400;500&family=Roboto+Condensed:wght@500&display=swap" rel="stylesheet">
<style>
  :root {
    --backdrop: #2a2a2a;
    --brand-red: #d62027;
    --brand-teal: #0b86a6;
    --brand-yellow: #f6b51e;
    --paper: #f1f1f1;
    --white: #ffffff;
  }
  html, body {
    margin: 0;
    padding: 0;
    width: 1200px;
    height: 960px;
    overflow: hidden;
    background: var(--backdrop);
    font-family: "Roboto", Arial, sans-serif;
  }
  .canvas {
    position: relative;
    width: 1200px;
    height: 960px;
  }
  .card {
    position: absolute;
    left: 320px;
    width: 600px;
    height: 342px;
  }
  /* Back of card */
  .card-back {
    top: 100px;
    background: var(--brand-red);
  }
  .card-back .brand-name {
    position: absolute;
    left: 0;
    right: 0;
    top: 140px;
    display: flex;
    justify-content: center;
    align-items: center;
    gap: 16px;
    color: var(--white);
    font-weight: 500;
    font-size: 36px;
    letter-spacing: 3px;
    text-transform: uppercase;
  }
  .brand-mark {
    width: 28px;
    height: 28px;
    background: currentColor;
  }
  .card-back .web {
    position: absolute;
    left: 0;
    right: 0;
    top: 298px;
    text-align: center;
    color: var(--white);
    font-size: 14px;
    letter-spacing: 5px;
  }
  /* Front of card */
  .card-front {
    top: 493px;
    background: var(--paper);
  }
  .card-front .panel-art {
    position: absolute;
    inset: 0;
  }
  .card-front .brand-name {
    position: absolute;
    left: 20px;
    width: 278px;
    top: 182px;
    display: flex;
    justify-content: center;
    align-items: center;
    gap: 10px;
    color: var(--brand-teal);
    font-weight: 500;
    font-size: 19px;
    letter-spacing: 2px;
    text-transform: uppercase;
  }
  .card-front .brand-name .brand-mark {
    width: 14px;
    height: 14px;
  }
  .contact {
    position: absolute;
    left: 362px;
    top: 64px;
    color: var(--white);
  }
  .contact .person-name {
    margin: 0;
    font-family: "Roboto Condensed", Arial, sans-serif;
    font-weight: 500;
    font-size: 24px;
    line-height: 1;
    color: var(--brand-yellow);
    text-transform: uppercase;
  }
  .contact .person-title {
    margin: 8px 0 0;
    font-weight: 500;
    font-size: 15px;
    text-transform: uppercase;
  }
  .contact .address {
    margin: 42px 0 0;
    font-style: normal;
    font-size: 14px;
    line-height: 18px;
  }
  .contact .address strong {
    font-weight: 500;
  }
  .contact-list {
    list-style: none;
    margin: 10px 0 0;
    padding: 0;
    font-size: 14px;
    line-height: 19px;
  }
  .contact-list li {
    display: flex;
    align-items: center;
    gap: 8px;
  }
  .contact-list svg {
    width: 13px;
    height: 13px;
    fill: var(--brand-yellow);
    flex: none;
  }
</style>
</head>
<body>
<main class="canvas">

  <section class="card card-back" aria-label="Card back">
    <div class="brand-name"><span class="brand-mark"></span>Haven Street Center</div>
    <div class="web">www.havenstreet.org</div>
  </section>

  <section class="card card-front" aria-label="Card front">
    <svg class="panel-art" width="600" height="342" viewBox="0 0 600 342">
      <polygon fill="var(--brand-teal)" points="322,0 600,0 600,342 322,342 322,112 342,87 322,62"/>
      <polyline fill="none" stroke="var(--brand-red)" stroke-width="3" points="318,0 318,62 338,87 318,112 318,342"/>
    </svg>

    <div class="brand-name"><span class="brand-mark"></span>Haven Street Center</div>

    <div class="contact">
      <h1 class="person-name">Dana Whitfield</h1>
      <p class="person-title">CEO/Founder</p>
      <address class="address">
        <strong>Haven Street Center</strong><br>
        2141 Alder Court<br>
        Fairbanks, Alaska 99701
      </address>
      <ul class="contact-list">
        <li>
          <svg viewBox="0 0 16 16" aria-hidden="true"><path d="M3.2 1l2.6 3.2-1.4 1.8c.9 2 2.6 3.7 4.6 4.6l1.8-1.4L14 11.8 12.6 14.6C6.8 14.2 1.8 9.2 1.4 3.4z"/></svg>
          412 555 0187
        </li>
        <li>
          <svg viewBox="0 0 16 16" aria-hidden="true"><path d="M1 3h14v1.2L8 8.6 1 4.2z M1 5.6l7 4.4 7-4.4V13H1z"/></svg>
          dana@havenstreet.org
        </li>
        <li>
          <svg viewBox="0 0 16 16" aria-hidden="true"><circle cx="8" cy="8" r="7"/><path d="M1 8h14M8 1c-3 3-3 11 0 14M8 1c3 3 3 11 0 14" stroke="var(--brand-teal)" stroke-width="1" fill="none"/></svg>
          www.havenstreet.org
        </li>
      </ul>
    </div>
  </section>

</main>
</body>
</html>
```